KTWG application splash screen

We need a 1024x768 image for use as an application splash screen.
The image will be displayed full screen on an 10 inch industrial PC 1024x768 screen while our application is launching. The image should convey that the application is "Waiting for connection to Wi-Fi access point..." and include a graphic of the industrial PC connected to the access point via an Ethernet cable. A list of troubleshooting steps should be included at the bottom of the image. The troubleshooting steps should not be the main focus of the image and should be shown in a smaller font (but still readable at 1024x768 displayed on a 10 inch screen).
I will include a mock up of the general idea of what we are looking for as well as image files for the industrial PC, a screenshot of our application to show on the PC's screen and the AP.
For general look and feel and a sense of corporate branding please review our website https://marrowgatesoilworks.example/. The splash screen should reflect corporate branding.
Target Market(s)
Users of our application
Industry/Entity Type
Agriculture
Look and feel

```html
<!DOCTYPE html>
<html lang="en">
<head>
<meta charset="utf-8">
<title>KTWG – Waiting for Wi-Fi access point</title>
<link rel="stylesheet" href="https://fonts.googleapis.com/css2?family=Poppins:wght@400;500;600;700&display=swap">
<style>
  :root {
    --sky-top: #5f7a52;
    --field-mid: #3f7a22;
    --field-deep: #2c6314;
    --brand-green: #2fb36a;
    --soil-dark: #1f1712;
    --soil-mid: #4a3a2e;
    --soil-light: #5e4b3d;
    --text-white: #ffffff;
    --device-body: #26282b;
    --device-screen: #dfe6dc;
    --ap-body: #eef0ef;
    --cable: #111111;
  }
  * { box-sizing: border-box; margin: 0; padding: 0; }
  html, body { width: 1200px; height: 900px; overflow: hidden; }
  body { font-family: "Poppins", sans-serif; color: var(--text-white); }

  .splash { position: relative; width: 1200px; height: 900px; overflow: hidden; }

  .field-scene {
    position: absolute; inset: 0 0 250px 0;
    background: linear-gradient(180deg, var(--sky-top) 0%, #56763f 22%, var(--field-mid) 45%, var(--field-deep) 100%);
  }
  .soil-scene {
    position: absolute; left: 0; right: 0; top: 620px; bottom: 0;
    background: linear-gradient(180deg, var(--soil-light) 0%, var(--soil-mid) 40%, var(--soil-dark) 100%);
  }
  .divider { position: absolute; left: 0; top: 592px; width: 1200px; height: 80px; }

  .brand { position: absolute; left: 45px; top: 38px; }
  .brand-name { font-weight: 700; font-size: 58px; line-height: 1; letter-spacing: 2px; }
  .brand-company { margin-top: 10px; font-size: 17px; font-weight: 500; border-bottom: 1px solid var(--text-white); padding-bottom: 3px; display: inline-block; }

  .status-title {
    position: absolute; left: 290px; width: 740px; top: 30px;
    text-align: center; font-weight: 600; font-size: 64px; line-height: 79px;
    white-space: nowrap;
  }

  .cab-computer {
    position: absolute; left: 53px; top: 281px; width: 287px; height: 246px;
    background: var(--device-body); border-radius: 14px;
  }
  .cab-computer .screen {
    position: absolute; left: 20px; top: 20px; width: 247px; height: 178px;
    background: linear-gradient(180deg, var(--device-screen), #c9d8c2); border-radius: 3px;
  }

  .ethernet-cable { position: absolute; left: 332px; top: 472px; width: 734px; height: 3px; background: var(--cable); }

  .access-point {
    position: absolute; left: 1052px; top: 252px; width: 50px; height: 212px;
    background: linear-gradient(90deg, #d6dad8, var(--ap-body) 50%, #cfd3d1);
    border-radius: 8px;
  }

  .label { position: absolute; font-weight: 600; text-align: center; }
  .label-cab { left: 40px; width: 300px; top: 533px; font-size: 23px; }
  .label-cable { left: 520px; width: 280px; top: 428px; font-size: 21px; }
  .label-ap { left: 940px; width: 250px; top: 492px; font-size: 22px; }
  .label-ap .model { display: block; font-size: 13px; font-weight: 500; margin-top: 2px; }

  .footer-mark {
    position: absolute; left: 42px; top: 770px;
    font-weight: 700; font-size: 44px; color: var(--brand-green);
  }

  .troubleshooting { position: absolute; left: 413px; top: 668px; width: 560px; }
  .troubleshooting h2 { font-size: 20px; font-weight: 700; margin-bottom: 20px; }
  .troubleshooting ul { list-style: none; font-size: 13.5px; line-height: 20.5px; }
  .troubleshooting li::before { content: "•"; margin-right: 6px; }
  .troubleshooting ul ul { margin-left: 40px; }
  .troubleshooting ul ul li::before { content: "◦"; margin-right: 6px; }
  .troubleshooting ul ul li { padding-left: 14px; text-indent: -14px; }
</style>
</head>
<body>
<main class="splash">
  <div class="field-scene" role="img" aria-label="Photo of a green crop field under a cloudy sky"></div>
  <div class="soil-scene" role="img" aria-label="Photo of freshly tilled dark soil rows"></div>
  <svg class="divider" viewBox="0 0 1200 80" aria-hidden="true">
    <polygon points="0,56 600,16 1200,56 1200,80 0,80" fill="var(--soil-mid)"/>
    <polygon points="0,44 600,2 1200,44 1200,58 600,18 0,58" fill="var(--brand-green)"/>
  </svg>

  <header class="brand">
    <div class="brand-name">KTWG</div>
    <div class="brand-company">Marrowgate Soil Works Inc.</div>
  </header>

  <h1 class="status-title">Waiting for<br>connection to Wi-Fi<br>access point...</h1>

  <div class="cab-computer" role="img" aria-label="Tractor cab computer showing the seeding application screen">
    <div class="screen"></div>
  </div>
  <div class="ethernet-cable"></div>
  <div class="access-point" role="img" aria-label="Outdoor Wi-Fi access point with two antennas"></div>

  <p class="label label-cab">Tractor cab computer</p>
  <p class="label label-cable">Ethernet cable</p>
  <p class="label label-ap">Wi-Fi Access Point<span class="model">NorLink AX300-Field</span></p>

  <div class="footer-mark">KTWG</div>

  <section class="troubleshooting">
    <h2>Troubleshooting steps:</h2>
    <ul>
      <li>This screen should only be visible for a short time on boot.</li>
      <li>If this screen stays visible for more than a minute:
        <ul>
          <li>Verify that when the cab computer is powered up the Wi-Fi Access Point (AP) is also powered up (indicated by green light on side of the AP).</li>
          <li>Check the Ethernet cable for damage and replace if damaged.</li>
          <li>Contact KTWG support for further assistance.</li>
        </ul>
      </li>
    </ul>
  </section>
</main>
</body>
</html>
```